Pine Hollow Haven Home Inc. Website Update

We have a couple of broken links such as the "contact us" and would like to add board members and a calendar of events. We are open to a new design.

```html
<!DOCTYPE html>
<html lang="en">
<head>
<meta charset="utf-8">
<title>Pine Hollow Haven Home Inc.</title>
<link href="https://fonts.googleapis.com/css2?family=Montserrat:wght@600;700;800&family=Open+Sans:wght@400;600;700&display=swap" rel="stylesheet">
<style>
:root{
  --pink:#dc1f7c;
  --ink:#1d1d1d;
  --body:#444;
  --blush:#f5f1f1;
  --blue:#1565c0;
  --blue-dark:#0d4f9e;
  --footer:#232323;
  --gold:#c9a227;
  --white:#fff;
}
*{margin:0;padding:0;box-sizing:border-box}
html,body{width:1200px;height:4401px;overflow:hidden}
body{position:relative;font-family:"Open Sans",Arial,sans-serif;color:var(--body);background:var(--white)}
.abs{position:absolute}
h1,h2,h3,h4,.nav a,.btn{font-family:"Montserrat",Arial,sans-serif}
.btn{display:inline-block;background:var(--pink);color:var(--white);font-weight:700;text-transform:uppercase;text-decoration:none;letter-spacing:.5px}
.section-title{font-size:30px;font-weight:800;color:var(--ink);text-transform:uppercase;text-align:center;letter-spacing:.5px}
.section-title.underlined span{border-bottom:4px solid var(--pink);padding-bottom:2px}

/* header */
.site-header{left:0;top:0;width:1200px;height:115px;background:var(--white)}
.brand{left:140px;top:6px;width:150px;height:150px;border-radius:50%;background:var(--white);box-shadow:0 3px 10px rgba(0,0,0,.18);display:flex;align-items:center;justify-content:center;text-align:center;z-index:3}
.brand-name{font-family:"Montserrat",sans-serif;font-weight:800;color:var(--pink);font-size:15px;line-height:1.2;width:110px}
.nav{left:330px;top:80px;display:flex;gap:26px}
.nav a{font-size:13px;font-weight:700;color:var(--ink);text-decoration:none;text-transform:uppercase}
.nav a.active{color:var(--pink);border-bottom:2px solid var(--pink);padding-bottom:3px}
.call{left:718px;top:24px;display:flex;align-items:center;gap:12px}
.call-icon{width:28px;height:28px;border-radius:50%;background:var(--pink);display:flex;align-items:center;justify-content:center}
.call small{display:block;font-size:11px;font-weight:700;color:var(--ink)}
.call strong{font-family:"Montserrat",sans-serif;font-size:19px;color:var(--ink)}
.site-header .btn{left:912px;top:24px;width:142px;height:38px;line-height:38px;text-align:center;font-size:13px}

/* hero */
.hero{left:0;top:115px;width:1200px;height:597px;background:linear-gradient(180deg,#6f7d8a 0%,#9aa39c 35%,#7d8f62 65%,#4f6b33 100%)}
.badge{left:668px;top:285px;width:118px;height:118px;border-radius:50%;background:var(--gold);border:6px solid #e9cc6a}
.hero-text{left:820px;top:270px;color:var(--white)}
.hero-text p{font-family:"Montserrat",sans-serif;font-weight:700;font-size:22px}
.hero-text h1{font-size:39px;font-weight:800;text-transform:uppercase;line-height:1.1;margin-top:4px}
.hero-text .btn{margin-top:22px;padding:11px 26px;font-size:14px}
.dots{left:548px;top:537px;display:flex;gap:14px;align-items:center}
.dots i{width:8px;height:8px;border-radius:50%;background:var(--white);display:block}
.dots i.on{width:14px;height:14px;border:3px solid var(--white);background:var(--pink)}

/* about */
.about{left:0;top:712px;width:1200px;height:720px;background:var(--blush)}
.about .section-title{position:absolute;top:68px;width:100%}
.about .lead{position:absolute;top:122px;left:350px;width:500px;text-align:center;font-size:16px;line-height:1.6;color:#333}
.divider-v{left:600px;top:240px;width:1px;height:380px;background:#ddd}
.divider-h{left:140px;top:438px;width:920px;height:1px;background:#ddd}
.service{display:flex;gap:30px;width:440px}
.service .icon{flex:0 0 126px;height:126px;border-radius:50%;background:var(--white);box-shadow:0 4px 14px rgba(0,0,0,.08);display:flex;align-items:center;justify-content:center}
.service h3{font-size:15px;font-weight:700;color:var(--ink);line-height:1.3;margin-top:6px}
.service p{font-size:13px;line-height:1.5;margin-top:8px;color:#555}

/* board */
.board{left:0;top:1432px;width:1200px;height:653px}
.board .section-title{position:absolute;top:58px;width:100%}
.member{width:220px;top:158px;height:425px;background:var(--white);box-shadow:0 2px 12px rgba(0,0,0,.08)}
.member .photo{height:250px}
.member .tag{position:absolute;left:12px;top:222px;width:178px;background:#9e9e9e;border-left:5px solid var(--pink);padding:6px 12px;color:var(--white);font-family:"Montserrat",sans-serif}
.member .tag b{display:block;font-size:13px}
.member .tag small{font-size:12px;font-weight:700}
.member p{margin:48px 18px 0;font-size:13px;line-height:1.5}
.small-btn{margin:14px 18px 0;padding:6px 14px;font-size:11px}

/* events */
.events{left:0;top:2085px;width:1200px;height:625px;background:var(--blush)}
.events .section-title{position:absolute;top:58px;width:100%}
.event{top:155px;width:280px;height:415px;background:var(--white)}
.event .photo{height:225px;position:relative}
.event .date{position:absolute;left:14px;top:150px;width:56px;padding:6px 0;background:var(--pink);color:var(--white);text-align:center;font-family:"Montserrat",sans-serif;line-height:1}
.event .date small{font-size:10px;font-weight:700;display:block}
.event .date b{font-size:28px;display:block;margin:3px 0}
.event h3{font-size:18px;font-weight:700;color:var(--ink);margin:26px 24px 0;line-height:1.25}
.event p{margin:10px 24px 0;font-size:13px;line-height:1.5}
.event .btn{margin:14px 24px 0;padding:6px 14px;font-size:11px}

/* testimonial */
.testimonial{left:0;top:2710px;width:1200px;height:465px;background:linear-gradient(180deg,var(--blue-dark),var(--blue))}
.testimonial .section-title{position:absolute;top:78px;width:100%;color:var(--white)}
.quote{left:375px;top:150px;width:450px;text-align:center;color:#e3eefb;font-size:18px;line-height:1.6}
.qmark{font-family:Georgia,serif;font-size:64px;color:var(--white);font-weight:700;line-height:1}
.avatar{left:570px;top:310px;width:60px;height:60px;border-radius:50%;background:#c9a58b;border:3px solid var(--white)}
.arrow{top:325px}
.testimonial .name{left:0;top:388px;width:1200px;text-align:center;color:var(--white);font-family:"Montserrat",sans-serif;font-weight:700;font-size:15px;text-transform:uppercase}

/* success */
.success{left:0;top:3175px;width:1200px;height:620px}
.success .photo{left:0;top:0;width:642px;height:615px;background:linear-gradient(135deg,#0d1b24 0%,#23424b 45%,#8a7a55 75%,#2c2c2c 100%)}
.success .panel{left:532px;top:90px;width:530px;height:380px;background:var(--white);padding:60px 40px 60px 45px}
.success h2{font-size:26px;font-weight:800;color:var(--ink);text-transform:uppercase;line-height:1.3}
.success p{font-size:16px;line-height:1.55;margin-top:18px;color:#444}
.success .btn{margin-top:28px;padding:12px 28px;font-size:20px}

/* accreditation */
.accred{left:140px;top:3708px;width:890px;height:232px;background:#eeeeee}
.accred-edge{left:1010px;top:3708px;width:20px;height:232px;background:var(--white);clip-path:polygon(0 0,100% 0,100% 100%,55% 100%)}
.seal{left:82px;top:56px;width:84px;height:84px;border-radius:50%;background:var(--gold);border:5px solid #e4c45c}
.seal-label{left:72px;top:150px;width:104px;text-align:center;font-family:"Montserrat",sans-serif;font-weight:800;color:#777;font-size:20px}
.accred .rule{left:228px;top:30px;width:1px;height:172px;background:#bbb}
.accred .copy{left:292px;top:42px;width:520px;font-size:18px;line-height:1.5;color:#333}
.accred .copy p+p{margin-top:18px}

/* footer */
.footer-line{left:0;top:4003px;width:1200px;height:6px;background:var(--pink)}
.site-footer{left:0;top:4009px;width:1200px;height:392px;background:var(--footer);color:#ddd}
.footer-brand{left:140px;top:58px;width:190px;height:190px;border-radius:50%;background:var(--white);display:flex;align-items:center;justify-content:center;text-align:center}
.footer-brand .brand-name{font-size:18px;width:140px}
.site-footer h4{font-size:13px;font-weight:700;color:var(--white);text-transform:uppercase;letter-spacing:.5px}
.fcol ul{list-style:none;margin-top:28px}
.contact-list li{display:flex;gap:14px;font-size:11px;line-height:1.6;margin-bottom:26px}
.menu-list li{font-size:11px;line-height:1.6;text-transform:uppercase}
.social-list li{display:flex;align-items:center;gap:10px;font-size:11px;margin-bottom:18px}
.social-list .dot{width:22px;height:22px;border-radius:50%;background:#1f6fd1;display:block}
.copyright{left:0;top:340px;width:1200px;text-align:center;font-size:11px;color:#bbb}
</style>
</head>
<body>

<header class="site-header abs">
  <div class="brand abs"><span class="brand-name">Pine Hollow Haven Home</span></div>
  <nav class="nav abs">
    <a class="active" href="#">Home</a><a href="#">About</a><a href="#">How You Can Help</a><a href="#">Services Offered</a><a href="#">Our Love of Pets</a><a href="#">Haven Walk</a><a href="#">Contact Us</a>
  </nav>
  <div class="call abs">
    <span class="call-icon"><svg width="14" height="14" viewBox="0 0 24 24"><path fill="#fff" d="M6.6 10.8a15.1 15.1 0 0 0 6.6 6.6l2.2-2.2c.3-.3.7-.4 1-.2 1.1.4 2.3.6 3.6.6.6 0 1 .4 1 1V20c0 .6-.4 1-1 1A17 17 0 0 1 3 4c0-.6.4-1 1-1h3.5c.6 0 1 .4 1 1 0 1.3.2 2.5.6 3.6.1.3 0 .7-.2 1z"/></svg></span>
    <div><small>CALL US</small><strong>555.214.7730</strong></div>
  </div>
  <a class="btn abs" href="#">Donate Now</a>
</header>

<section class="hero abs" role="img" aria-label="Photo of the two-storey house with a wide porch under a flowering tree on a green lawn">
  <div class="badge abs"></div>
  <div class="hero-text abs">
    <p>WELCOME TO</p>
    <h1>Pine Hollow<br>Haven Inc</h1>
    <a class="btn" href="#">Read More</a>
  </div>
  <div class="dots abs"><i></i><i></i><i class="on"></i><i></i><i></i></div>
</section>

<section class="about abs">
  <h2 class="section-title">We are Pine Hollow Haven Home</h2>
  <p class="lead">With the help of our community, we have raised over 1000 girls and counting! Some of the services we offer include</p>
  <div class="divider-v abs"></div>
  <div class="divider-h abs"></div>

  <div class="service abs" style="left:138px;top:240px">
    <div class="icon"><svg width="60" height="50" viewBox="0 0 60 50"><rect x="6" y="10" width="40" height="22" rx="3" fill="#dc1f7c"/><rect x="4" y="32" width="52" height="6" fill="#dc1f7c"/><rect x="6" y="38" width="4" height="8" fill="#dc1f7c"/><rect x="50" y="38" width="4" height="8" fill="#dc1f7c"/><rect x="46" y="16" width="10" height="16" fill="#dc1f7c"/></svg></div>
    <div><h3>Room, Board, and<br>Watchful Oversight</h3><p>Our agency contracts with the Regional Youth Welfare Office and the Family Support Bureau in each county in Georgia to provide Room, Board, and Watchful Oversight to girls ages 12- 18.</p></div>
  </div>
  <div class="service abs" style="left:660px;top:240px">
    <div class="icon"><svg width="60" height="52" viewBox="0 0 60 52"><path d="M4 26 30 4l26 22" stroke="#dc1f7c" stroke-width="5" fill="none"/><rect x="12" y="24" width="36" height="24" fill="none" stroke="#dc1f7c" stroke-width="5"/><rect x="26" y="32" width="9" height="16" fill="#dc1f7c"/></svg></div>
    <div><h3>Transitional Living<br>Services</h3><p>Transitional Living Services are available to youth who have demonstrated a desire to gain knowledge in the areas of Independent Living Skills between the ages of 16 and 18.</p></div>
  </div>
  <div class="service abs" style="left:138px;top:478px">
    <div class="icon"><svg width="48" height="54" viewBox="0 0 48 54"><circle cx="24" cy="16" r="12" fill="#dc1f7c"/><path d="M2 54c0-14 10-22 22-22s22 8 22 22z" fill="#dc1f7c"/></svg></div>
    <div><h3>Independent Living<br>Services</h3><p>Independent Living is a unique opportunity for girls ages 18 to 21 to expand upon and practice Independent Living Skills while learning to become active participants in their community.</p></div>
  </div>
  <div class="service abs" style="left:660px;top:478px">
    <div class="icon"><svg width="52" height="52" viewBox="0 0 52 52"><rect x="4" y="16" width="44" height="10" fill="#dc1f7c"/><rect x="8" y="28" width="36" height="22" fill="#dc1f7c"/><rect x="23" y="16" width="6" height="34" fill="#fff"/><path d="M26 16c-6-12-16-8-12-2zM26 16c6-12 16-8 12-2z" fill="none" stroke="#dc1f7c" stroke-width="3"/></svg></div>
    <div><h3>Foster Gift Shop</h3><p>When the economy began cutting jobs, the Pine Hollow Haven Home got busy trying to find a solution for employment for our girls. In order to be eligible for the Independent Living Home, our girls needed to have employment of at least 9-25 hours per week</p></div>
  </div>
</section>

<section class="board abs">
  <h2 class="section-title underlined"><span>Board Members</span></h2>
  <article class="member abs" style="left:120px">
    <div class="photo" role="img" aria-label="Portrait of a board member against a pink background" style="background:linear-gradient(160deg,#f2a9b9,#d97e93)"></div>
    <div class="tag"><b>MORGAN</b><small>Executive Manager</small></div>
    <p>Lorem Ipsum is simply dummy text of the printing and types etting.</p>
    <a class="btn small-btn" href="#">Read More</a>
  </article>
  <article class="member abs" style="left:367px">
    <div class="photo" role="img" aria-label="Portrait of a board member outdoors" style="background:linear-gradient(160deg,#6f5b3e,#3d3322)"></div>
    <div class="tag"><b>MORGAN</b><small>Executive Manager</small></div>
    <p>Lorem Ipsum is simply dummy text of the printing and types etting.</p>
    <a class="btn small-btn" href="#">Read More</a>
  </article>
  <article class="member abs" style="left:615px">
    <div class="photo" role="img" aria-label="Portrait of a smiling board member" style="background:linear-gradient(160deg,#6f8566,#3b4d38)"></div>
    <div class="tag"><b>MORGAN</b><small>Executive Manager</small></div>
    <p>Lorem Ipsum is simply dummy text of the printing and types etting.</p>
    <a class="btn small-btn" href="#">Read More</a>
  </article>
  <article class="member abs" style="left:862px">
    <div class="photo" role="img" aria-label="Portrait of a board member on a dark background" style="background:linear-gradient(160deg,#3c3c3c,#1a1a1a)"></div>
    <div class="tag"><b>MORGAN</b><small>Executive Manager</small></div>
    <p>Lorem Ipsum is simply dummy text of the printing and types etting.</p>
    <a class="btn small-btn" href="#">Read More</a>
  </article>
</section>

<section class="events abs">
  <h2 class="section-title underlined"><span>Latest Events</span></h2>
  <article class="event abs" style="left:140px">
    <div class="photo" role="img" aria-label="Photo of a group of girls in formal dresses at an event" style="background:linear-gradient(160deg,#7a5a6a,#2e2430)"><div class="date"><small>MARCH</small><b>07</b><small>THU</small></div></div>
    <h3>Lorem Ipsum is simply dummy text.</h3>
    <p>Lorem Ipsum is simply dummy text of the printing and types etting. indu stry's standard dummy.</p>
    <a class="btn" href="#">Read More</a>
  </article>
  <article class="event abs" style="left:460px">
    <div class="photo" role="img" aria-label="Photo of a crowd at a night party under blue lights" style="background:linear-gradient(160deg,#2b3aa8,#120f3d)"><div class="date"><small>MARCH</small><b>08</b><small>FRI</small></div></div>
    <h3>Lorem Ipsum is simply dummy text.</h3>
    <p>Lorem Ipsum is simply dummy text of the printing and types etting. indu stry's standard dummy.</p>
    <a class="btn" href="#">Read More</a>
  </article>
  <article class="event abs" style="left:775px">
    <div class="photo" role="img" aria-label="Photo of a rooftop terrace overlooking the sea" style="background:linear-gradient(180deg,#9fc7ea,#e2e6e8 60%,#b7aa98)"><div class="date"><small>MARCH</small><b>09</b><small>SAT</small></div></div>
    <h3>Lorem Ipsum is simply dummy text.</h3>
    <p>Lorem Ipsum is simply dummy text of the printing and types etting. indu stry's standard dummy.</p>
    <a class="btn" href="#">Read More</a>
  </article>
</section>

<section class="testimonial abs">
  <h2 class="section-title underlined"><span>What Our Girls Say</span></h2>
  <span class="qmark abs" style="left:335px;top:140px">&ldquo;</span>
  <p class="quote abs">Emotionally healed a lot and I felt supported. I learned how to cook, budget, get a job, buy a car, pay bills, community service and helping others. I would not have gotten here without the Pine Hollow Haven.</p>
  <span class="qmark abs" style="left:780px;top:265px">&rdquo;</span>
  <svg class="arrow abs" style="left:500px" width="14" height="24" viewBox="0 0 14 24"><path d="M12 2 2 12l10 10" stroke="#fff" stroke-width="2.5" fill="none"/></svg>
  <div class="avatar abs" role="img" aria-label="Small portrait of the quoted girl"></div>
  <svg class="arrow abs" style="left:686px" width="14" height="24" viewBox="0 0 14 24"><path d="m2 2 10 10L2 22" stroke="#fff" stroke-width="2.5" fill="none"/></svg>
  <p class="name abs">Danielle</p>
</section>

<section class="success abs">
  <div class="photo abs" role="img" aria-label="Photo of cupped hands holding coins with a small green sprout"></div>
  <div class="panel abs">
    <h2>Over 500 success stories<br>and growing strong.</h2>
    <p>We appreciate donations from our community! It is because of the hearts of those around us that we're able to do what we do.</p>
    <a class="btn" href="#">Donate Now</a>
  </div>
</section>

<section class="accred abs">
  <div class="seal abs"></div>
  <div class="seal-label abs">RCSB</div>
  <div class="rule abs"></div>
  <div class="copy abs">
    <p>Residential Care Standards Board certified since 2009</p>
    <p>To learn more about our RCSB accreditation, please visit www.rcsb-standards.org.</p>
  </div>
</section>
<div class="accred-edge abs"></div>

<div class="footer-line abs"></div>
<footer class="site-footer abs">
  <div class="footer-brand abs"><span class="brand-name">Pine Hollow Haven Home</span></div>
  <div class="fcol abs" style="left:420px;top:64px;width:200px">
    <h4>Contact Us</h4>
    <ul class="contact-list">
      <li><svg width="10" height="14" viewBox="0 0 10 14"><path d="M5 0a5 5 0 0 0-5 5c0 4 5 9 5 9s5-5 5-9a5 5 0 0 0-5-5z" fill="#fff"/></svg><span>418 Birchwood Ln, Millbrook,<br>GA 30999, USA</span></li>
      <li><svg width="12" height="12" viewBox="0 0 24 24"><path fill="#fff" d="M6.6 10.8a15.1 15.1 0 0 0 6.6 6.6l2.2-2.2c.3-.3.7-.4 1-.2 1.1.4 2.3.6 3.6.6.6 0 1 .4 1 1V20c0 .6-.4 1-1 1A17 17 0 0 1 3 4c0-.6.4-1 1-1h3.5c.6 0 1 .4 1 1 0 1.3.2 2.5.6 3.6.1.3 0 .7-.2 1z"/></svg><span>555.214.7730</span></li>
      <li><svg width="13" height="10" viewBox="0 0 13 10"><rect width="13" height="10" fill="#fff"/><path d="m0 0 6.5 5L13 0" stroke="#232323" fill="none"/></svg><span>hello@pinehollowhaven.org</span></li>
    </ul>
  </div>
  <div class="fcol abs" style="left:708px;top:64px;width:160px">
    <h4>Menu</h4>
    <ul class="menu-list"><li>Home</li><li>About</li><li>How You Can Help</li><li>Services Offered</li><li>Our Love of Pets</li><li>Haven Walk</li><li>Contact Us</li></ul>
  </div>
  <div class="fcol abs" style="left:915px;top:64px;width:160px">
    <h4>Connect With Us</h4>
    <ul class="social-list">
      <li><span class="dot"></span>Community Page</li>
      <li><span class="dot" style="background:#22a3e6"></span>News Feed</li>
      <li><span class="dot" style="background:#1a1a1a;border:1px solid #555"></span>Network</li>
    </ul>
  </div>
  <p class="copyright abs">Copyrights © 2019 All Rights Reserved</p>
</footer>

</body>
</html>
```